Design website for new email startup

We are starting a company called Pingo.QZ (it will live at http://pingo.qz).

We would like the main landing page for our site designed. We have provided a very simple wireframe to help provide direction for the content it should include, but we do not expect the designers to adhere to it at all - we encourage unique ideas. There is some sample text in the wireframe - this does not have to be used, but may provide ideas.

We provide an easy way for people to manage email for a custom domain name. For example if you own "yourhouseword.example" you can point your DNS records to us and we'll make it easy to have emails addressed to your domain get forwarded to your existing email (gmail, etc). Folks running blogs, and other small sites can quickly setup email addresses for their domains and manage them in one place.

(For technical folks, we have you point your dns mx records to us, hence the name. That way all your email hits us and we can redirect it wherever you want. We make it easy to manage a single domain or a bunch of domains. Many domain registrars offer this service for a fee, and have clumsy management tools. We provide a robust simple toolset for free, as well as premium options).

The goal of the landing page is to get folks into the signup flow. The second priority flow is to have them take a look at the premium plan offerings.

We may offer the winning designer additional work for the remainder of the site design.
Updates

I've changed this project to a committed payment.  It is no longer refundable.  Thank you.

Target Market(s)

Bloggers, podcasters, designers, app developers - people who are a little tech savvy.

Industry/Entity Type

It Company

Font styles to use
Sans Serif

Colors

Designer to choose colors to be used in the design.

Requirements
Must have
• A full fidelity mockup (comp) of the landing page including the source file (psd, ai, etc).

Some sort of logo treatment for the pingo.qz brand

A call to action for signup, such as the suggested 'Get Started Here'
Nice to have
• A hip startup feel

Incorporation of the email theme

Give the impression it is simple, easy and fast

```html
<!DOCTYPE html>
<html lang="en">
<head>
<meta charset="utf-8">
<title>Pingo.QZ – Email for your domain</title>
<link rel="stylesheet" href="https://fonts.googleapis.com/css2?family=Roboto:wght@400;500;700;900&display=swap">
<style>
  :root {
    --black: #000000;
    --white: #ffffff;
    --brand-blue: #4a6cf2;
    --link-blue: #1a3fd0;
    --cta-top: #1f4fe8;
    --cta-bottom: #0b33c4;
    --hero-light: #7d9ae8;
    --hero-mid: #3f63d8;
    --hero-dark: #22348f;
    --panel-gray: #f1f1f1;
    --card-border: #dcdcdc;
    --icon-gray: #6a6a6a;
    --text-dark: #222222;
    --text-body: #444444;
  }
  * { box-sizing: border-box; margin: 0; padding: 0; }
  html, body { width: 1200px; height: 954px; overflow: hidden; }
  body { font-family: "Roboto", Arial, sans-serif; background: var(--white); position: relative; }

  .site-header { position: absolute; top: 0; left: 0; width: 1200px; height: 60px; background: var(--black); }
  .brand { position: absolute; left: 133px; top: 12px; font-size: 33px; font-weight: 700; color: var(--brand-blue); letter-spacing: -0.5px; }
  .main-nav { position: absolute; right: 131px; top: 20px; color: var(--white); font-size: 16px; font-weight: 500; }
  .main-nav a { color: var(--white); text-decoration: none; }
  .main-nav .sep { margin: 0 8px; }

  .hero { position: absolute; top: 71px; left: 0; width: 1200px; height: 516px; overflow: hidden; }
  .hero-art { position: absolute; inset: 0;
    background: radial-gradient(ellipse at 75% 35%, #c9d6f8 0%, transparent 40%),
                linear-gradient(120deg, var(--hero-light) 0%, var(--hero-mid) 45%, var(--hero-dark) 100%); }
  .benefits { position: absolute; left: 133px; top: 88px; width: 570px; height: 167px; background: rgba(150,150,150,0.55); list-style: none; padding: 30px 0 0 8px; }
  .benefits li { color: var(--white); font-size: 15.5px; height: 35px; display: flex; align-items: flex-start; gap: 8px; }
  .benefits svg { flex: none; margin-top: 3px; }
  .btn-start { position: absolute; left: 133px; top: 297px; width: 199px; height: 42px; background: var(--white); color: var(--link-blue); font-size: 16px; display: flex; align-items: center; justify-content: center; border-radius: 2px; text-decoration: none; }
  .plans-bar { position: absolute; left: 133px; top: 386px; width: 936px; height: 94px; background: var(--white); }
  .plans-bar p { position: absolute; left: 16px; top: 21px; width: 660px; font-size: 16.5px; line-height: 26px; color: var(--text-dark); }
  .btn-plans { position: absolute; left: 719px; top: 24px; width: 196px; height: 47px; border-radius: 3px; background: linear-gradient(var(--cta-top), var(--cta-bottom)); color: var(--white); font-size: 16px; display: flex; align-items: center; justify-content: center; text-decoration: none; }

  .guides { position: absolute; top: 587px; left: 0; width: 1200px; height: 224px; background: var(--panel-gray); }
  .guide-card { position: absolute; top: 40px; width: 445px; height: 143px; border: 1px solid var(--card-border); background: linear-gradient(#ffffff 30%, #e6e6e6); }
  .guide-card.first { left: 133px; }
  .guide-card.second { left: 623px; }
  .guide-icon { position: absolute; left: 19px; top: 18px; width: 105px; height: 105px; border-radius: 16px; background: var(--icon-gray); }
  .guide-card h3 { position: absolute; left: 139px; top: 30px; width: 300px; font-size: 12.5px; line-height: 18px; font-weight: 400; color: var(--link-blue); }
  .guide-card p { position: absolute; left: 139px; width: 295px; font-size: 11px; line-height: 18px; color: var(--text-body); }
  .guide-card.first p { top: 65px; }
  .guide-card.second p { top: 83px; }

  .site-footer { position: absolute; top: 836px; left: 0; width: 1200px; height: 118px; background: var(--black); color: var(--white); text-align: center; }
  .social { position: absolute; top: -19px; left: 0; width: 1200px; display: flex; justify-content: center; gap: 6px; }
  .social a { width: 38px; height: 38px; border-radius: 50%; background: var(--white); border: 2px solid var(--black); color: var(--black); font-size: 8.5px; font-weight: 700; display: flex; align-items: center; justify-content: center; text-decoration: none; }
  .footer-nav { position: absolute; top: 46px; width: 1200px; font-size: 14px; font-weight: 500; }
  .footer-nav a { color: var(--white); text-decoration: none; }
  .footer-nav .sep { margin: 0 6px; }
  .copyright { position: absolute; top: 84px; width: 1200px; font-size: 11.5px; color: #dddddd; }
</style>
</head>
<body>
  <header class="site-header">
    <div class="brand">PINGO.QZ</div>
    <nav class="main-nav"><a href="#">How It Works</a><span class="sep">|</span><a href="#">Support</a><span class="sep">|</span><a href="#">Login</a></nav>
  </header>

  <section class="hero">
    <div class="hero-art" role="img" aria-label="Blue photo of envelopes flying into an open mailbox with at-sign symbols"></div>
    <ul class="benefits">
      <li><svg width="14" height="12" viewBox="0 0 14 12"><path d="M1 6.5 L5 10 L13 1.5" fill="none" stroke="#fff" stroke-width="2.4"/></svg>We make email esay.</li>
      <li><svg width="14" height="12" viewBox="0 0 14 12"><path d="M1 6.5 L5 10 L13 1.5" fill="none" stroke="#fff" stroke-width="2.4"/></svg>Give us five minutes and well get you email from your domain.</li>
      <li><svg width="14" height="12" viewBox="0 0 14 12"><path d="M1 6.5 L5 10 L13 1.5" fill="none" stroke="#fff" stroke-width="2.4"/></svg>Easily forward mail from your custom domain in name wherever you want it.</li>
      <li><svg width="14" height="12" viewBox="0 0 14 12"><path d="M1 6.5 L5 10 L13 1.5" fill="none" stroke="#fff" stroke-width="2.4"/></svg>You take yhe mail well keep the spam.</li>
    </ul>
    <a class="btn-start" href="#">GET STARTED FREE</a>
    <div class="plans-bar">
      <p>Somewhere we need a link to plan/pricing options,although the free tier is encouraged for initial signup.</p>
      <a class="btn-plans" href="#">COMPARE PLANS</a>
    </div>
  </section>

  <section class="guides">
    <article class="guide-card first">
      <div class="guide-icon" role="img" aria-label="Wrench and screwdriver tools icon"></div>
      <h3>How to configure your SkyShield DNS to use pingo.qz</h3>
      <p>We provide an easy way for people to manage email for a custom domain name. For technical folks, we have you point your dns mx record..........................</p>
    </article>
    <article class="guide-card second">
      <div class="guide-icon" role="img" aria-label="Key and tag icon"></div>
      <h3>Use pingo.qz with your NameHarbor domain registration for reliableemail forwarding</h3>
      <p>We provide an easy way for people to manage email for a custom domain name. For technical folks,...................</p>
    </article>
  </section>

  <footer class="site-footer">
    <div class="social">
      <a href="#" aria-label="Chirp">Chirp</a>
      <a href="#" aria-label="Feed">Feed</a>
      <a href="#" aria-label="Vidz">Vidz</a>
      <a href="#" aria-label="Pals">Pals</a>
      <a href="#" aria-label="Circl">Circl</a>
    </div>
    <nav class="footer-nav"><a href="#">About us</a><span class="sep">//</span><a href="#">How it Works</a><span class="sep">//</span><a href="#">Privacy &amp; Security</a><span class="sep">//</span><a href="#">Contact Us</a></nav>
    <div class="copyright">© 2014 all copyrights are reserved</div>
  </footer>
</body>
</html>
```